Presentation Folder with inside Pockets

We need a Presentation Folder with inside pockets. The size of the folder will be 9" x 12" and will be printed on the cover, the back and the inside folder flaps. The design will be very simple and consist of our logo (large) on the front cover and our logo (smaller) and contact information on the back. We are open to various colors that you think may go along with our logo. When you display your work, show the front, back and inside.

Target Market(s)

Pharmaceutical Companies

Industry/Entity Type

Work

Requirements
Should not have
• please do not add stock medical photos.

```html
<!DOCTYPE html>
<html lang="en">
<head>
<meta charset="utf-8">
<title>Meridian Trials Inc. – Presentation Folder</title>
<link rel="stylesheet" href="https://fonts.googleapis.com/css2?family=Open+Sans:wght@400;600;700&display=swap">
<style>
  :root {
    --stage: #020202;
    --blue-light: #1b93d2;
    --blue-mid: #15699f;
    --blue-dark: #0c3f6a;
    --green: #8dc63f;
    --green-light: #9fcf3f;
    --green-dark: #5c9731;
    --paper: #f5f5f5;
    --paper-shade: #e4e4e4;
    --ink: #1a1a1a;
    --ink-soft: #555555;
    --white: #ffffff;
  }
  * { margin: 0; padding: 0; box-sizing: border-box; }
  html, body { width: 1200px; height: 998px; overflow: hidden; background: var(--stage); }
  body { font-family: "Open Sans", Arial, sans-serif; position: relative; }

  .folder-back {
    position: absolute; left: 69px; top: 40px; width: 599px; height: 692px;
    background: linear-gradient(180deg, var(--blue-light) 0%, var(--blue-mid) 55%, var(--blue-dark) 100%);
    color: var(--white);
  }
  .spine-rule { position: absolute; left: 671px; top: 40px; width: 4px; height: 692px; background: var(--green); }
  .spine-gap { position: absolute; left: 668px; top: 40px; width: 3px; height: 692px; background: var(--white); }
  .folder-front {
    position: absolute; left: 675px; top: 40px; width: 433px; height: 692px;
    background: linear-gradient(180deg, var(--paper) 0%, var(--paper-shade) 100%);
  }

  .front-badge {
    position: absolute; left: 610px; top: 77px; width: 92px; height: 92px;
    border-radius: 50%; background: var(--white);
  }
  .front-name {
    position: absolute; left: 712px; top: 106px; width: 330px;
    font-weight: 700; font-size: 25px; letter-spacing: 0.5px; color: var(--ink); white-space: nowrap;
  }
  .front-web {
    position: absolute; left: 16px; bottom: 16px;
    font-size: 13px; letter-spacing: 3px; color: var(--ink-soft);
  }

  .back-badge {
    position: absolute; left: 229px; top: 436px; width: 66px; height: 66px;
    border-radius: 50%; background: var(--green);
  }
  .back-name {
    position: absolute; left: 0; top: 546px; width: 599px; text-align: center;
    font-weight: 700; font-size: 25px; letter-spacing: 0.5px; color: var(--white);
  }
  .back-divider {
    position: absolute; left: 51px; top: 613px; width: 408px; height: 1px;
    background: linear-gradient(90deg, transparent, rgba(255,255,255,.45), transparent);
  }
  .back-contact {
    position: absolute; left: 0; top: 634px; width: 599px; text-align: center;
    font-size: 12.5px; line-height: 25px;
  }
  .back-contact .item { display: inline-flex; align-items: center; gap: 5px; margin: 0 4px; }
  .back-contact svg { width: 13px; height: 13px; }

  .pockets { position: absolute; left: 0; top: 0; width: 1200px; height: 998px; }

  .card {
    position: absolute; top: 797px; width: 202px; height: 115px;
    background: var(--white); color: var(--ink); font-size: 5.5px; line-height: 8px;
  }
  .card-left { left: 210px; }
  .card-right { left: 765px; }
  .card-name { position: absolute; left: 10px; top: 19px; font-weight: 700; font-size: 9px; white-space: nowrap; }
  .card-contact { position: absolute; left: 10px; top: 65px; }
  .card-address { position: absolute; left: 10px; top: 91px; }
  .card-holder { position: absolute; left: 138px; top: 67px; width: 60px; text-align: center; font-weight: 600; font-size: 6px; }
</style>
</head>
<body>

  <section class="folder-back">
    <div class="back-badge"></div>
    <div class="back-name">MERIDIAN TRIALS INC.</div>
    <div class="back-divider"></div>
    <div class="back-contact">
      <span class="item">
        <svg viewBox="0 0 16 16" aria-hidden="true"><circle cx="8" cy="8" r="7" fill="none" stroke="#fff" stroke-width="1.4"/><path d="M5.5 4.5l1.5 1.6-.8 1.1c.6 1.2 1.4 2 2.6 2.6l1.1-.8 1.6 1.5-1 1.2c-2.9-.4-5.6-3.1-6-6z" fill="#fff"/></svg>
        +1-555-014-2290
      </span>
      <span class="item">
        <svg viewBox="0 0 16 16" aria-hidden="true"><rect x="1.5" y="4" width="13" height="9" rx="1" fill="#fff"/><path d="M2 4.5l6 5 6-5" fill="none" stroke="#15699f" stroke-width="1.3"/></svg>
        hello@meridiantrials.net
      </span>
      <br>
      Meridian Trials Inc. 84 Linden Avenue, Westbrook, NY 11602
    </div>
  </section>

  <div class="spine-gap"></div>
  <div class="spine-rule"></div>

  <section class="folder-front">
    <div class="front-web">www.meridiantrials.net</div>
  </section>
  <div class="front-badge"></div>
  <div class="front-name">MERIDIAN TRIALS INC.</div>

  <svg class="pockets" viewBox="0 0 1200 998" aria-hidden="true">
    <defs>
      <radialGradient id="pocket-blue" cx="0.55" cy="0.45" r="0.6">
        <stop offset="0" stop-color="#1f93d4"/>
        <stop offset="1" stop-color="#0d4d7e"/>
      </radialGradient>
      <radialGradient id="pocket-green" cx="0.6" cy="0.35" r="0.6">
        <stop offset="0" stop-color="#a2d142"/>
        <stop offset="1" stop-color="#5e9a32"/>
      </radialGradient>
    </defs>
    <path class="pocket-left" d="M69 733 L588 733 L578 950 Q576 963 562 963 L68 963 L25 948 L25 746 Z" fill="url(#pocket-blue)"/>
    <path class="pocket-right" d="M590 733 L1108 733 L1153 747 L1153 948 L1112 963 L624 963 Q612 963 610 950 Z" fill="url(#pocket-green)"/>
    <g class="crop-marks" stroke="#9aa5ad" stroke-width="0.8">
      <path d="M198 787 L216 803 M422 787 L404 803 M198 922 L216 906 M422 922 L404 906"/>
      <path d="M753 787 L771 803 M977 787 L959 803 M753 922 L771 906 M977 922 L959 906"/>
    </g>
  </svg>

  <div class="card card-left">
    <div class="card-name">MERIDIAN TRIALS INC.</div>
    <div class="card-contact">+1-555-014-2290<br>hello@meridiantrials.net</div>
    <div class="card-address">Meridian Trials Inc. 84 Linden Avenue<br>Westbrook, NY 11602</div>
    <div class="card-holder">Your Name<br>Title</div>
  </div>

  <div class="card card-right">
    <div class="card-name">MERIDIAN TRIALS INC.</div>
    <div class="card-contact">+1-555-014-2290<br>hello@meridiantrials.net</div>
    <div class="card-address">Meridian Trials Inc. 84 Linden Avenue<br>Westbrook, NY 11602</div>
    <div class="card-holder">Your Name<br>Title</div>
  </div>

</body>
</html>
```